Crestline Plaque & Medal Unique Business Card Design

Recently selected a new logo design and waiting to recieve print files. I've attached image for your review. We are a trophies and awards company that provides engraving on trophies, plaques, name plates, name tags, desk sets, medals, acrylics, and signage.

We are located in Monroe, Louisiana and provide this service with computerized & laser engraving equipment.

Target Market(s)

Corporate, Sport, Church, and Special Events

Industry/Entity Type

Business

Contact Information for Business Card

I'd like to see the following list on the card: Trophies, Plaques, Name Plates, Name Tags, Desk Sets, Medals, Certificates... this is accomplished with Computerized & Laser Engraving

Colors
0555a3
ec1f27
ffffff

Requirements
Must have
• I like either single or double sided. If a design can be created with a frosted card stock I'd consider single. Must be Red, White, and Blue. Dwight Palmer - Owner, 412 W 8th Ave, Monroe, La 71208 office 318-555-0148 fax 318-555-0163 email: info@crestlineplaquemedal.example, and website: www.crestlineplaquemedal.example

```html
<!DOCTYPE html>
<html lang="en">
<head>
<meta charset="utf-8">
<title>Crestline Plaque &amp; Medal – Business Card</title>
<link rel="stylesheet" href="https://fonts.googleapis.com/css2?family=Open+Sans:wght@400;600&display=swap">
<style>
  :root {
    --backdrop: #3b3531;
    --card: #111112;
    --brand-blue: #2f7fd6;
    --deep-blue: #0555a3;
    --brand-red: #ec1f27;
    --mark-grey: #3a3a3c;
    --service-grey: #55555a;
    --white: #ffffff;
  }
  * { margin: 0; padding: 0; box-sizing: border-box; }
  html, body { width: 1200px; height: 844px; overflow: hidden; }
  body {
    background: var(--backdrop);
    font-family: "Open Sans", Arial, sans-serif;
    position: relative;
  }
  .card {
    position: absolute;
    top: 273px;
    width: 520px;
    height: 298px;
    background: var(--card);
    border-radius: 3px;
    box-shadow: 0 10px 24px rgba(0,0,0,.45);
    overflow: hidden;
  }
  .card--front { left: 50px; }
  .card--back { left: 630px; }

  .brand {
    position: absolute;
    left: 0; right: 0;
    display: flex;
    flex-direction: column;
    align-items: center;
  }
  .card--front .brand { top: 48px; }
  .card--back .brand { top: 104px; }
  .brand__row { display: flex; align-items: center; gap: 10px; }
  .brand__dot {
    width: 14px; height: 14px; border-radius: 50%;
    background: var(--brand-red);
  }
  .brand__name {
    font-size: 27px;
    font-weight: 600;
    color: var(--brand-blue);
    letter-spacing: .2px;
  }
  .brand__rule {
    width: 300px; height: 2px; margin-top: 6px;
    background: var(--brand-blue);
  }
  .card--back .brand__dot { background: var(--mark-grey); }
  .card--back .brand__name { color: var(--mark-grey); }
  .card--back .brand__rule { background: var(--mark-grey); }

  .services {
    position: absolute;
    left: 40px; right: 40px; top: 178px;
    text-align: center;
    font-size: 12px;
    line-height: 1.6;
    color: var(--service-grey);
  }
  .services__method { font-weight: 600; }

  .person {
    position: absolute;
    left: 40px; top: 150px;
    color: var(--brand-blue);
  }
  .person__name { font-size: 22px; font-weight: 600; line-height: 1.1; }
  .person__title { font-size: 14px; color: var(--brand-red); margin: 2px 0 0 28px; }
  .person__address { font-size: 15px; line-height: 1.25; margin-top: 14px; }

  .contacts {
    position: absolute;
    left: 244px; top: 150px;
    list-style: none;
    font-size: 13px;
    color: var(--brand-blue);
  }
  .contacts li { display: flex; align-items: center; gap: 7px; height: 21px; white-space: nowrap; }
  .contacts svg { width: 12px; height: 12px; flex: none; fill: var(--brand-red); }
</style>
</head>
<body>

<section class="card card--front" aria-label="Business card front">
  <div class="brand">
    <div class="brand__row">
      <span class="brand__dot"></span>
      <span class="brand__name">Crestline Plaque &amp; Medal</span>
    </div>
    <div class="brand__rule"></div>
  </div>

  <div class="person">
    <p class="person__name">Dwight Palmer</p>
    <p class="person__title">Owner</p>
    <p class="person__address">412 W 8th Ave<br>Monroe, La 71208</p>
  </div>

  <ul class="contacts">
    <li>
      <svg viewBox="0 0 12 12" aria-hidden="true"><path d="M1 4c0-2 2-3 5-3s5 1 5 3l-2 1-1-1H4L3 5zM3 6h6l1 5H2z"/></svg>
      318-555-0148
    </li>
    <li>
      <svg viewBox="0 0 12 12" aria-hidden="true"><path d="M3 1h5v3H3zM1 5h10v5H9v2H3v-2H1zM4 8v3h4V8z"/></svg>
      318-555-0163
    </li>
    <li>
      <svg viewBox="0 0 12 12" aria-hidden="true"><path d="M1 3h10v7H1zM1.5 3.5 6 7l4.5-3.5"/></svg>
      info@crestlineplaquemedal.example
    </li>
    <li>
      <svg viewBox="0 0 12 12" aria-hidden="true"><path d="M7 1l4 4-2 2-1-1 1-1-2-2-3 3 2 2-1 1-3-3zM5 11L1 7l2-2 1 1-1 1 2 2 3-3-2-2 1-1 3 3z"/></svg>
      www.crestlineplaquemedal.example
    </li>
  </ul>
</section>

<section class="card card--back" aria-label="Business card back">
  <div class="brand">
    <div class="brand__row">
      <span class="brand__dot"></span>
      <span class="brand__name">Crestline Plaque &amp; Medal</span>
    </div>
    <div class="brand__rule"></div>
  </div>
  <div class="services">
    <p>Trophies · Plaques · Name Plates · Name Tags · Desk Sets · Medals · Certificates</p>
    <p class="services__method">Computerized &amp; Laser Engraving</p>
  </div>
</section>

</body>
</html>
```